Business Card for Coastal Tundrabridge Advisory

We need a business card for Coastal Tundrabridge Advisory. The company website address is provided below. The company logo is attached. We provide specialized permafrost services to the mining, transportation, and oil & gas industries. The card should be prepared for:
Matthias Korhonen, PhD.
Coastal Tundrabridge Advisory
PO Box 418259
Quillwater, Alaska 99642
Direct: +1-907-555-0143
Email: mkorhonen@tundrabridgeadvisory.example
Website: www.coastaltundrabridgeadvisory.example

```html
<!DOCTYPE html>
<html lang="en">
<head>
<meta charset="utf-8">
<title>Coastal Tundrabridge Advisory – Business Card</title>
<link href="https://fonts.googleapis.com/css2?family=Montserrat:wght@400;700&display=swap" rel="stylesheet">
<style>
  :root {
    --ink: #141a22;
    --paper: #ffffff;
    --backdrop: #e9e7e4;
    --shadow: rgba(0, 0, 0, 0.18);
  }
  * { margin: 0; padding: 0; box-sizing: border-box; }
  html, body {
    width: 1200px; height: 900px; overflow: hidden;
    background: var(--backdrop);
    font-family: "Montserrat", Arial, sans-serif;
    color: var(--ink);
  }
  .sheet {
    width: 1200px; height: 900px;
    display: flex; flex-direction: column; align-items: center; justify-content: center;
    gap: 30px;
  }
  .card {
    width: 700px; height: 400px;
    background: var(--paper);
    box-shadow: 0 6px 18px var(--shadow);
    display: flex; flex-direction: column; align-items: center;
    text-align: center;
  }
  .card--front { justify-content: center; position: relative; }
  .brand-name {
    font-weight: 700; text-transform: uppercase; color: var(--ink);
  }
  .card--front .brand-name { font-size: 31px; letter-spacing: 3px; }
  .social-row {
    position: absolute; bottom: 48px; left: 50%; transform: translateX(-50%);
    display: flex; gap: 6px;
  }
  .social-dot { width: 20px; height: 20px; border-radius: 50%; background: var(--ink); }

  .card--back { padding-top: 30px; }
  .card--back .brand-name { font-size: 17px; letter-spacing: 2px; margin-bottom: 18px; }
  .holder-name { font-size: 25px; font-weight: 700; line-height: 1.2; }
  .holder-company { font-size: 15px; margin-top: 2px; }
  .icon { width: 24px; height: 24px; display: block; }
  .pin { margin: 10px auto 6px; }
  .address { font-size: 15px; line-height: 1.35; }
  .contact-icons { display: flex; gap: 6px; margin: 12px 0 6px; }
  .contact-lines { font-size: 15px; line-height: 1.45; }
</style>
</head>
<body>
<main class="sheet">
  <section class="card card--front">
    <p class="brand-name">Coastal Tundrabridge Advisory</p>
    <div class="social-row" aria-label="Social media links">
      <span class="social-dot"></span><span class="social-dot"></span><span class="social-dot"></span><span class="social-dot"></span><span class="social-dot"></span>
    </div>
  </section>

  <section class="card card--back">
    <p class="brand-name">Coastal Tundrabridge Advisory</p>
    <h1 class="holder-name">Matthias Korhonen, PhD</h1>
    <p class="holder-company">Coastal Tundrabridge Advisory</p>
    <svg class="icon pin" viewBox="0 0 24 24" aria-hidden="true">
      <circle cx="12" cy="12" r="12" fill="var(--ink)"/>
      <path d="M12 5a4.5 4.5 0 0 0-4.5 4.5c0 3.3 4.5 8.5 4.5 8.5s4.5-5.2 4.5-8.5A4.5 4.5 0 0 0 12 5z" fill="#fff"/>
      <circle cx="12" cy="9.5" r="1.7" fill="var(--ink)"/>
    </svg>
    <p class="address">Coastal Tundrabridge Advisory<br>PO Box 418259</p>
    <div class="contact-icons">
      <svg class="icon" viewBox="0 0 24 24" aria-hidden="true">
        <circle cx="12" cy="12" r="12" fill="var(--ink)"/>
        <path d="M8.2 6.5l2 2.2-1.1 1.6c.8 1.7 2 2.9 3.7 3.7l1.6-1.1 2.2 2-1.2 1.9c-4.3-.4-8.1-4.2-8.5-8.5z" fill="#fff"/>
      </svg>
      <svg class="icon" viewBox="0 0 24 24" aria-hidden="true">
        <circle cx="12" cy="12" r="12" fill="var(--ink)"/>
        <rect x="6" y="8" width="12" height="8.5" rx="1" fill="#fff"/>
        <path d="M6.5 8.5l5.5 4.3 5.5-4.3" fill="none" stroke="var(--ink)" stroke-width="1.2"/>
      </svg>
      <svg class="icon" viewBox="0 0 24 24" aria-hidden="true">
        <circle cx="12" cy="12" r="12" fill="var(--ink)"/>
        <circle cx="12" cy="12" r="6" fill="none" stroke="#fff" stroke-width="1.3"/>
        <ellipse cx="12" cy="12" rx="2.6" ry="6" fill="none" stroke="#fff" stroke-width="1.1"/>
        <path d="M6 12h12" stroke="#fff" stroke-width="1.1"/>
      </svg>
    </div>
    <p class="contact-lines">
      +1-907-555-0143<br>
      mkorhonen@tundrabridgeadvisory.example<br>
      www.coastaltundrabridgeadvisory.example
    </p>
  </section>
</main>
</body>
</html>
```